WordPress Design for both website and landing page for an expert

I need a clean and stylish design for my new website. I work as an expert (see attached file WHY HOW WHAT), my product is expert opinion (reports) for company evaluations You can use all of the attached pictures colored or black / white. The person is me, you can add other pictures, if you want. The design should be clean and stylish, so you could use white, black, gray, silver and / or one additional color. I have added an idea about my website, see attached file CONCEPT WEBSITE If you have any more information, please do not hesitate to contact us 'Hesitate to ask me ...

```html
<!DOCTYPE html>
<html lang="de">
<head>
<meta charset="utf-8">
<title>Lars Brenning – Sachverständiger für Firmenbewertungen</title>
<link rel="stylesheet" href="https://fonts.googleapis.com/css2?family=Lato:wght@300;400;700&display=swap">
<style>
:root{
  --ink:#1c1c1c;
  --text:#4a4a4a;
  --muted:#777;
  --white:#fff;
  --paper:#fff;
  --light:#e8e8e8;
  --mid:#8a8a8a;
  --dark:#2a2a2a;
  --line:#d8d8d8;
}
*{margin:0;padding:0;box-sizing:border-box}
html,body{width:1200px;height:2826px;overflow:hidden;background:var(--paper)}
body{font-family:'Lato',sans-serif;color:var(--text);position:relative}

/* hero */
.hero{position:absolute;left:0;top:0;width:1200px;height:658px;
  background:linear-gradient(90deg,#5d5d5d 0%,#8c8c8c 40%,#b5b5b5 62%,#d9d9d9 80%,#c4c4c4 100%)}
.hero-photo{position:absolute;inset:0;background:radial-gradient(ellipse 300px 420px at 770px 360px,rgba(245,245,245,.55),rgba(245,245,245,0) 70%)}
.brand{position:absolute;left:160px;top:58px;width:230px;text-align:center;color:var(--white);
  font-weight:300;font-size:25px;letter-spacing:5px;text-transform:uppercase}
.nav{position:absolute;left:441px;top:40px;display:flex;gap:30px}
.nav a{color:var(--white);text-decoration:none;font-size:16px;text-transform:uppercase;position:relative}
.nav a.active::before{content:"";position:absolute;left:0;right:0;top:-40px;height:5px;background:var(--white)}
.hero h1{position:absolute;left:158px;top:252px;color:var(--white);font-weight:400;font-size:40px;line-height:46px;text-transform:uppercase}
.hero p{position:absolute;left:158px;top:356px;width:500px;color:var(--white);font-size:22px;line-height:28px;font-weight:300}
.dots{position:absolute;left:158px;top:436px;display:flex;gap:8px}
.dots span{width:13px;height:13px;border-radius:50%;background:var(--white);border:2px solid var(--white)}
.dots span.on{background:transparent}

/* reasons */
.mark{position:absolute;font-size:15px;letter-spacing:2px;color:var(--mid);text-transform:uppercase;text-align:center}
.reasons-title{position:absolute;left:0;width:1200px;top:728px;text-align:center;font-size:32px;font-weight:400;color:var(--ink);line-height:37px}
.reason{position:absolute;width:290px}
.reason svg{display:block}
.reason h3{margin-top:30px;font-size:21px;font-weight:400;color:var(--ink)}
.reason p{margin-top:14px;font-size:15.5px;line-height:23px;color:var(--text)}

/* faq */
.faq{position:absolute;left:0;top:1147px;width:1200px;height:532px;
  background:linear-gradient(160deg,#4a4a4a 0%,#2c2c2c 40%,#1e1e1e 70%,#3a3a3a 100%)}
.faq-notch{position:absolute;left:430px;top:0}
.faq h2{position:absolute;left:0;width:1200px;top:58px;text-align:center;color:var(--white);font-size:36px;font-weight:400}
.acc{position:absolute;left:145px;width:919px;border:2px solid var(--white);color:var(--white);font-size:17.5px;
  display:flex;align-items:center;padding:0 30px 0 32px;justify-content:space-between;line-height:21px}
.acc b{font-weight:700;font-size:26px}

/* content */
.frame{position:absolute;left:143px;top:1735px;width:277px;height:234px;background:#8f8f8f}
.photo{position:absolute;left:162px;top:1760px;width:390px;height:278px;
  background:linear-gradient(135deg,#b9c3cc 0%,#dde3e8 45%,#9aa5ae 100%)}
.copy{position:absolute;left:584px;top:1760px;width:480px;font-size:20.5px;line-height:32px;color:var(--ink)}
.copy p+p{margin-top:12px}

/* promise */
.promise{position:absolute;left:0;top:2127px;width:1200px;height:507px;
  background:linear-gradient(90deg,#e6e6e6 0%,#f0f0f0 20%,#dcdcdc 50%,#bdbdbd 75%,#a9a9a9 100%)}
.promise-band{position:absolute;left:0;top:0;width:141px;height:507px;background:var(--light)}
.promise-person{position:absolute;left:700px;top:20px;width:330px;height:487px;
  background:linear-gradient(180deg,#b08f80 0%,#3a3a3a 35%,#2a2a2a 100%);border-radius:150px 150px 0 0}
.promise-text{position:absolute;left:166px;top:0;width:500px;height:507px;z-index:1}
.promise h4{position:absolute;left:0;font-size:24px;font-weight:700;color:var(--ink);text-transform:uppercase}
.promise p{position:absolute;left:0;width:500px;font-size:17.5px;line-height:28px;color:var(--ink)}

/* footer */
.fnav{position:absolute;left:0;width:1200px;top:2672px;display:flex;justify-content:center;gap:30px}
.fnav a{color:var(--ink);text-decoration:none;font-size:16.5px;text-transform:uppercase}
.copyr{position:absolute;left:0;width:1200px;top:2706px;text-align:center;font-size:14px;color:var(--muted)}
.social{position:absolute;left:0;width:1200px;top:2756px;display:flex;justify-content:center;gap:28px}
.social span{width:16px;height:16px;border-radius:50%;background:var(--ink)}
</style>
</head>
<body>

<header class="hero">
  <div class="hero-photo" role="img" aria-label="Portrait photo of the expert leaning on a railing in a white shirt, concrete wall behind"></div>
  <div class="brand">Lars Brenning</div>
  <nav class="nav">
    <a class="active" href="#">Home</a>
    <a href="#">What I do</a>
    <a href="#">Why I do it &amp; how I do it</a>
    <a href="#">About me</a>
    <a href="#">Contact</a>
  </nav>
  <h1>Sachverständiger für<br>Firmenbewertungen</h1>
  <p>Sie benötigen ein Gutachten zur Ermittlung des Wertes Ihres Unternehmens</p>
  <div class="dots"><span class="on"></span><span></span><span></span><span></span></div>
</header>

<section>
  <div class="mark" style="left:0;width:1200px;top:690px">Lars Brenning</div>
  <h2 class="reasons-title">3 REASONS, WHY YOU SHOULD<br>WORK WITH ME</h2>

  <div class="reason" style="left:164px;top:836px">
    <svg width="70" height="70" viewBox="0 0 70 70" fill="none" stroke="#1c1c1c" stroke-width="2.5">
      <circle cx="35" cy="35" r="32"/><circle cx="35" cy="35" r="24" stroke-dasharray="3 4"/>
      <line x1="35" y1="35" x2="48" y2="24"/><circle cx="35" cy="35" r="4" fill="#1c1c1c"/>
      <rect x="26" y="46" width="18" height="8"/>
    </svg>
    <h3>1. SCHNELL</h3>
    <p>Sie bekommen Ihr Gutachten zeitnah (innerhalb von max. 21 Tagen nach Zugang aller benötigten Unterlagen)</p>
  </div>

  <div class="reason" style="left:480px;top:836px">
    <svg width="72" height="70" viewBox="0 0 72 70" fill="none" stroke="#1c1c1c" stroke-width="2.5">
      <path d="M14 6h46v56H14z"/><path d="M8 6h12v8H8z"/>
      <line x1="22" y1="18" x2="52" y2="18"/><line x1="22" y1="26" x2="52" y2="26"/>
      <line x1="22" y1="34" x2="44" y2="34"/><line x1="22" y1="42" x2="36" y2="42"/>
      <circle cx="50" cy="48" r="7"/><path d="M46 54l-2 10 6-3 6 3-2-10"/>
    </svg>
    <h3>2. ZERTIFIZIERT</h3>
    <p>Sie erhalten ein qualifiziertes und belastbares Gutachten von einem zertifizierten Sachverständigen (höchste Akzeptanz bei allen Parteien)</p>
  </div>

  <div class="reason" style="left:810px;top:840px;width:260px">
    <svg width="60" height="70" viewBox="0 0 60 70" fill="none" stroke="#1c1c1c" stroke-width="2.5">
      <path d="M18 66V52C8 46 4 36 6 26 9 12 20 4 33 4c14 0 24 10 24 24l-1 8 4 8-6 2v8c0 4-3 6-7 6h-7v6"/>
      <circle cx="31" cy="28" r="8"/><circle cx="31" cy="28" r="14" stroke-dasharray="5 4"/>
    </svg>
    <h3>3. VERSTÄNDLICH</h3>
    <p>Ihr Gutachten wird für Sie logisch und nachvollziehbar sein und kein "Fachchinesisch" enthalten</p>
  </div>
</section>

<section class="faq">
  <svg class="faq-notch" width="340" height="34" viewBox="0 0 340 34"><path d="M0 0H340C300 0 290 2 200 30Q170 40 140 30C50 2 40 0 0 0Z" fill="#fff"/></svg>
  <div class="mark" style="left:0;width:1200px;top:6px;font-size:13px">Lars Brenning</div>
  <h2>FAQ</h2>
  <div class="acc" style="top:138px;height:49px"><span>What are the buying motives of the customers?</span><b>+</b></div>
  <div class="acc" style="top:193px;height:49px"><span>Was sind die Kaufmotive der Kunden?</span><b>+</b></div>
  <div class="acc" style="top:247px;height:49px"><span>Sie wollen Anteile Ihres Unternehmens oder ihr gesamtes Unternehmen verkaufen?</span><b>+</b></div>
  <div class="acc" style="top:302px;height:49px"><span>Sie wollen Ihr Unternehmen auf Ihre Erben übertragen und benötigen eine Bewertung für das Finanzamt?</span><b>+</b></div>
  <div class="acc" style="top:360px;height:66px"><span>Sie müssen im Rahmen einer Trennung/Scheidung jemanden ausbezahlen und benötigen eine<br>Bemessungsgrundlage?</span><b>−</b></div>
</section>

<section>
  <div class="frame"></div>
  <div class="photo" role="img" aria-label="Photo of hands working with financial charts and a tablet on a desk"></div>
  <div class="copy">
    <p>Lassen Sie Ihr Unternehmen von einem qualifizerten Sachverständigen bewerten und gehen somit vielen (unnötigen) Streitereien aus dem Weg.</p>
    <p>Merke: Die Kosten für ein Gutachten sind immer überproportional günstiger als die Kosten für Rechtsstreitigkeiten. Und das losgelöst von der psychischen Belastung einer solchen Auseinandersetzung ...</p>
  </div>
</section>

<section class="promise">
  <div class="promise-band"></div>
  <div class="promise-person" role="img" aria-label="Photo of the expert in a dark suit standing in a bright office hallway"></div>
  <div class="promise-text">
    <h4 style="top:115px">My quality promise:</h4>
    <p style="top:149px">should the advised date for the preparation of the report be exceeded, you will receive the report free of chare (I waive my fee)</p>
    <h4 style="top:267px">Mein Qualitätsversprechen:</h4>
    <p style="top:300px">Sollte der avisierte Termin für die Erstellung des Gutachtens überschritten werden, erhalten Sie das Gutachten absolut kostenfrei! (Ich verzichte auf mein Honorar)</p>
  </div>
</section>

<footer>
  <nav class="fnav">
    <a href="#">Home</a>
    <a href="#">What I do</a>
    <a href="#">Why I do it &amp; how I do it</a>
    <a href="#">About me</a>
    <a href="#">Contact</a>
  </nav>
  <div class="copyr">© 2018 Company Name&nbsp; All right reserved</div>
  <div class="social" aria-label="Social media links"><span></span><span></span><span></span></div>
</footer>

</body>
</html>
```